Tech Savy small Business accountant business card design

We need a business card for a new company based in the cloud. We provide tax, business advisory, accounting, information technology solutions and back office functions to small businesses. We offer fixed fee packages with add on services as you need them. By harnessing technology we simplify small business operational processes providing valuable time and information for small business owners to grow their business. In the logo (bluvoria) we want to be able to see bluv and experts. The final design should communicate achieving growth dreams and balance (ie life and $).
Updates
This project has been temporarily placed on hold until I finalize "Tech Savy small Business accountant needs a logo". I invite all designers to submit on this logo project. Once my logo is finalized I will resume this business card contest. Thanks Added Wednesday, March 19, 2014
This project has been temporarily placed on hold until I finalize "Tech Savy small Business accountant logo". I invite all designers to submit on this logo project. Once my logo is finalized I will resume this business card contest. Thanks Added Thursday, March 20, 2014
Target Market(s)
Small Business (Revenue $500,000, more than 3 employees) owners.
Industry/Entity Type
Small Business
Contact Information for Business Card
Marcy Elwind (Principal)
Accountant, Tax Agent.
TEL | 0417 683 912
EMAIL | Marcy.Elwind@bluvoria.com.au
WEB | www.bluvoria.com.au
Look and feel

```html
<!DOCTYPE html>
<html lang="en">
<head>
<meta charset="utf-8">
<title>bluvoria business card</title>
<link href="https://fonts.googleapis.com/css2?family=Open+Sans:wght@400;600;700&display=swap" rel="stylesheet">
<style>
  :root {
    --page: #ecebe8;
    --white: #ffffff;
    --paper: #f4f4f5;
    --band: #d9dadd;
    --grey-light: #8f9197;
    --grey-dark: #74767c;
    --blue: #1fa9dc;
    --ink-grey: #6d6f74;
    --text-light: #f2f3f5;
  }
  * { margin: 0; padding: 0; box-sizing: border-box; }
  html, body { width: 1200px; height: 780px; overflow: hidden; }
  body {
    background: var(--page);
    font-family: "Open Sans", Arial, sans-serif;
    position: relative;
  }
  .card {
    position: absolute;
    top: 235px;
    width: 540px;
    height: 309px;
    overflow: hidden;
    box-shadow: 0 6px 18px rgba(0,0,0,0.18);
  }
  .card-front { left: 40px; background: var(--paper); }
  .card-back {
    left: 620px;
    background: radial-gradient(ellipse at 50% 40%, var(--grey-light), var(--grey-dark));
  }
  .front-shapes { position: absolute; inset: 0; }
  .brand {
    position: absolute;
    font-weight: 700;
    letter-spacing: -1px;
    line-height: 1;
  }
  .tagline {
    position: absolute;
    font-weight: 400;
    line-height: 1;
  }
  .card-front .brand { left: 28px; top: 118px; font-size: 50px; color: var(--blue); }
  .card-front .tagline { left: 32px; top: 178px; font-size: 12.5px; color: var(--ink-grey); }
  .contact {
    position: absolute;
    right: 22px;
    top: 34px;
    text-align: right;
    color: var(--text-light);
  }
  .contact-name { font-size: 23px; font-weight: 600; color: var(--blue); line-height: 1.1; }
  .contact-role { font-size: 13px; line-height: 1.45; }
  .contact-role:first-of-type { margin-top: 4px; }
  .contact-lines { margin-top: 14px; }
  .contact-line {
    font-size: 12.5px;
    line-height: 1.6;
    display: flex;
    justify-content: flex-end;
    align-items: center;
    gap: 7px;
  }
  .contact-icon {
    width: 14px;
    height: 14px;
    background: var(--blue);
    border-radius: 2px;
    flex: none;
  }
  .contact-icon svg { display: block; width: 14px; height: 14px; }
  .icon-spacer { width: 14px; flex: none; }
  .card-back .brand {
    left: 0; right: 0; top: 112px;
    text-align: center;
    font-size: 60px;
    color: var(--white);
  }
  .card-back .tagline {
    left: 0; right: 0; top: 186px;
    text-align: center;
    font-size: 14px;
    color: #e4e5e8;
  }
</style>
</head>
<body>

<section class="card card-front" aria-label="Business card front">
  <svg class="front-shapes" viewBox="0 0 540 309" preserveAspectRatio="none">
    <defs>
      <linearGradient id="front-grey" x1="0" y1="0" x2="1" y2="1">
        <stop offset="0" stop-color="#9a9ca1"/>
        <stop offset="1" stop-color="#76787e"/>
      </linearGradient>
    </defs>
    <polygon points="252,0 274,0 354,309 332,309" fill="var(--band)"/>
    <polygon points="274,0 540,0 540,309 354,309" fill="url(#front-grey)"/>
    <line x1="250" y1="0" x2="330" y2="309" stroke="var(--blue)" stroke-width="1.5"/>
  </svg>

  <div class="brand">bluvoria</div>
  <div class="tagline">Your business and accounting partner</div>

  <div class="contact">
    <div class="contact-name">Marcy Elwind</div>
    <div class="contact-role">(Principal)</div>
    <div class="contact-role">Accountant, Tax Agent</div>
    <div class="contact-lines">
      <div class="contact-line">0417 683 912
        <span class="contact-icon"><svg viewBox="0 0 14 14"><path d="M4 3.2l1.6 0 .6 2-1 .8a6 6 0 0 0 2.8 2.8l.8-1 2 .6v1.6c0 .5-.4.8-.9.8A7 7 0 0 1 3.2 4.1c0-.5.3-.9.8-.9z" fill="#fff"/></svg></span>
      </div>
      <div class="contact-line">Marcy.Elwind@bluvoria.com.au
        <span class="contact-icon"><svg viewBox="0 0 14 14"><rect x="3" y="4.5" width="8" height="5.5" fill="none" stroke="#fff" stroke-width="1"/><path d="M3 4.5l4 3 4-3" fill="none" stroke="#fff" stroke-width="1"/></svg></span>
      </div>
      <div class="contact-line">www.bluvoria.com.au
        <span class="contact-icon"><svg viewBox="0 0 14 14"><circle cx="7" cy="7" r="3.8" fill="none" stroke="#fff" stroke-width="1"/><path d="M3.2 7h7.6M7 3.2v7.6" stroke="#fff" stroke-width=".8"/></svg></span>
      </div>
      <div class="contact-line">Kestrel Bay NSW Australia<span class="icon-spacer"></span></div>
    </div>
  </div>
</section>

<section class="card card-back" aria-label="Business card back">
  <div class="brand">bluvoria</div>
  <div class="tagline">Your business and accounting partner</div>
</section>

</body>
</html>
```